New boutique hotel for tourists, with hint of art deco styling

This is a new, soon to be completed, boutique hotel in Sydney. A letterhead with a logo is required. Less emphasis on the word "boutique". Perhaps the word could be screened to be lighter in colour (or print intensity). Would like a simple, clear, easy-to read, sans serif type face. The information on the letterhead is:
Mrs Tolliver Boutique Hotel
412 Quenby Street,
Larchmere, NSW, 2047
Australia
Tel: +61 2 9468-0000
mrstolliverhotel@quelmail.example
mrstolliverhotel.example.au
ABN 47 902 365 184

Target Market(s)

travellers, tourists, various ages

Industry/Entity Type

Hospitality

Contact Information for Business Card

Mrs Tolliver Boutique Hotel
412 Quenby Street,
Larchmere, NSW, 2047
Telephone: (02) 9468-0000
www.mrstolliverhotel.example.au
mrstolliverhotel@quelmail.example
ABN 47 902 365 184

Logo Text

suggest playing with the letter "T"

Font styles to use
Sans Serif

Colors
3176b5

Requirements
Must have
• ABN to be very small.
• Must be clear, easy to read and in a sans serif typeface, please!
Nice to have
• The word "Boutique" should be less intense in appearance to the rest of the name, or even "Boutique Hotel" can have less prominence than "Mrs Tolliver".
Should not have
• No serif typeface. Sans serif only will be accepted.

```html
<!DOCTYPE html>
<html lang="en">
<head>
<meta charset="utf-8">
<title>Mrs Tolliver Boutique Hotel – Stationery</title>
<link rel="stylesheet" href="https://fonts.googleapis.com/css2?family=Open+Sans:wght@400;600&display=swap">
<style>
  :root {
    --brand-blue: #3176b5;
    --brand-blue-deep: #2a66a8;
    --ink: #2b2b2b;
    --ink-soft: #6a6a6a;
    --paper: #ececec;
    --card-white: #f4f4f4;
    --rule: #8a8a8a;
    --backdrop: #e4e1dc;
    --card-blue-text: #9aa3ad;
    --signature-ink: #a9c4e6;
  }
  * { box-sizing: border-box; margin: 0; padding: 0; }
  html, body { width: 1200px; height: 900px; overflow: hidden; }
  body {
    position: relative;
    background: var(--backdrop);
    font-family: "Open Sans", Arial, sans-serif;
    color: var(--ink);
  }

  /* Letterhead */
  .letterhead {
    position: absolute;
    left: 458px; top: 22px;
    width: 535px; height: 694px;
    background: var(--paper);
  }
  .brand {
    position: absolute;
    color: var(--brand-blue-deep);
    font-weight: 400;
    line-height: 1;
  }
  .brand__name { display: block; }
  .brand__tag { display: block; letter-spacing: 0.22em; }

  .letterhead .brand { left: 70px; top: 46px; }
  .letterhead .brand__name { font-size: 25px; }
  .letterhead .brand__tag { font-size: 10px; margin-top: 5px; }

  .letter {
    position: absolute;
    left: 70px; top: 158px;
    width: 399px;
  }
  .letter__greeting { font-size: 12.5px; margin-bottom: 30px; }
  .letter__para {
    font-size: 10px;
    line-height: 15px;
    text-align: justify;
    text-align-last: justify;
    margin-bottom: 15px;
  }
  .letter__closing {
    position: absolute;
    right: 66px; top: 518px;
    font-size: 10.5px;
  }
  .letter__signature {
    position: absolute;
    right: 66px; top: 536px;
    width: 48px; height: 20px;
    background: linear-gradient(90deg, transparent, var(--signature-ink) 30%, var(--signature-ink) 70%, transparent);
    opacity: 0.55;
    border-radius: 10px;
  }

  .letter-footer {
    position: absolute;
    left: 70px; top: 638px;
    width: 399px;
    border-top: 1px solid var(--rule);
    padding-top: 4px;
    display: flex;
    font-size: 6px;
    color: var(--ink-soft);
  }
  .letter-footer__brand {
    width: 42px;
    font-size: 7px;
    line-height: 1.2;
    color: var(--ink-soft);
    border-right: 1px solid var(--rule);
    padding-right: 4px;
    height: 24px;
  }
  .letter-footer__details { padding-left: 10px; line-height: 11px; }
  .letter-footer__label { color: var(--brand-blue); font-weight: 600; }
  .letter-footer__gap { margin-left: 10px; }
  .letter-abn {
    position: absolute;
    left: 70px; top: 674px;
    font-size: 5px;
    color: var(--ink-soft);
  }

  /* Business cards */
  .card {
    position: absolute;
    top: 708px;
    width: 256px; height: 150px;
  }
  .card--front { left: 76px; background: var(--card-white); }
  .card--back { left: 356px; background: var(--brand-blue); }

  .card--front .brand { left: 16px; top: 20px; }
  .card--front .brand__name { font-size: 15px; }
  .card--front .brand__tag { font-size: 6.5px; margin-top: 3px; }

  .card__address {
    position: absolute;
    left: 16px; top: 98px;
    font-size: 6.5px;
    line-height: 7.5px;
    color: var(--ink);
  }
  .card__contacts {
    position: absolute;
    right: 18px; top: 99px;
    font-size: 6.5px;
    line-height: 11px;
    text-align: right;
  }
  .card__contact { display: flex; align-items: center; justify-content: flex-end; gap: 4px; }
  .card__dot {
    width: 7px; height: 7px;
    border-radius: 50%;
    background: #7f9fc7;
    display: inline-block;
  }
  .card__abn {
    position: absolute;
    left: 16px; top: 137px;
    font-size: 4.5px;
    color: var(--ink-soft);
  }

  .card--back .brand {
    left: 0; right: 0; top: 48px;
    text-align: center;
    color: var(--card-blue-text);
  }
  .card--back .brand__name { font-size: 19px; }
  .card--back .brand__tag { font-size: 7px; margin-top: 4px; }
</style>
</head>
<body>

  <article class="letterhead">
    <div class="brand">
      <span class="brand__name">Mrs Tolliver</span>
      <span class="brand__tag">Boutique Hotel</span>
    </div>

    <div class="letter">
      <p class="letter__greeting">Dear Mr. Pemberton,</p>
      <p class="letter__para">Lorem ipsum dolor sit amet, consectetur adipiscing elit. Donec orci purus, luctus vitae dignissim eu, iaculis sed purus. Vivamus faucibus, ipsum nec aliquet viverra, leo mauris condimentum ligula, sit amet sagittis enim ligula quis arcu. Nam egestas tortor id nisi porttitor mattis. In tortor ante, ultricies in suscipit a, tempus non massa. Vivamus et auctor mi. Fusce vel massa nulla. Phasellus nec eros mauris, et scelerisque orci.</p>
      <p class="letter__para">Donec malesuada orci vitae nulla accumsan porta a id massa. Quisque accumsan iaculis magna sit amet fringilla. Maecenas consequat, magna eget tincidunt semper, odio nibh rutrum mi, id feugiat ante nisi eu risus. Vestibulum nunc orci, rhoncus a placerat in, ultricies in mi. Cras mattis varius eros, vel fringilla nisi suscipit eget. Quisque scelerisque sagittis nulla at porttitor.</p>
      <p class="letter__para">Sed id augue vitae urna euismod commodo aliquet a quam. Pellentesque arcu velit, cursus et malesuada ut, consequat et diam. Nullam erat sem, rhoncus id ullamcorper vitae, rhoncus et arcu. In ultricies ultricies nulla, ut rutrum nisi iaculis at. Donec eu magna a metus ornare faucibus. Fusce aliquet faucibus ultricies. Morbi semper, est id tincidunt gravida, sem arcu adipiscing lacus, ac bibendum nulla leo eu purus. Quisque nec diam sed risus consectetur a ccumsan quis quis nibh. Vestibulum id purus lorem.</p>
    </div>

    <p class="letter__closing">Sincerely,</p>
    <div class="letter__signature" role="img" aria-label="Handwritten signature"></div>

    <footer class="letter-footer">
      <div class="letter-footer__brand">Mrs Tolliver</div>
      <div class="letter-footer__details">
        <div><span class="letter-footer__label">Address:</span> 412 Quenby Street, Larchmere, NSW, 2047, Australia</div>
        <div><span class="letter-footer__label">Mob:</span> +61 2 9468-0000
          <span class="letter-footer__gap letter-footer__label">Email:</span> mrstolliverhotel@quelmail.example
          <span class="letter-footer__gap letter-footer__label">Website:</span> mrstolliverhotel.example.au</div>
      </div>
    </footer>
    <p class="letter-abn">ABN 47 902 365 184</p>
  </article>

  <section class="card card--front">
    <div class="brand">
      <span class="brand__name">Mrs Tolliver</span>
      <span class="brand__tag">Boutique Hotel</span>
    </div>
    <address class="card__address" style="font-style:normal">
      412 Quenby Street,<br>Larchmere, NSW, 2047<br>Australia
    </address>
    <div class="card__contacts">
      <div class="card__contact">+61 2 9468-0000 <span class="card__dot"></span></div>
      <div class="card__contact">mrstolliverhotel@quelmail.example <span class="card__dot"></span></div>
      <div class="card__contact">mrstolliverhotel.example.au <span class="card__dot"></span></div>
    </div>
    <p class="card__abn">ABN 47 902 365 184</p>
  </section>

  <section class="card card--back">
    <div class="brand">
      <span class="brand__name">Mrs Tolliver</span>
      <span class="brand__tag">Boutique Hotel</span>
    </div>
  </section>

</body>
</html>
```